New Brochure for existing Virtual Reality Amusement Arena

I need a two sided half page brochure for my arcade. it needs to say what we do and what we have to offer. It basically needs to be a paper copy of all the information thats on my website www.vexmora-kin.com
Please check that as it is very informative!
Industry/Entity Type
Entertainment
Colors
Designer to choose colors to be used in the design.
Requirements
Must have
- Color. I have uploaded an old brochure I had made, but now we have a new company and new logo, please make it similar to that. Please pull all pics from my website www.vexmora-kin.com
Should not have
- useless information

```html
<!DOCTYPE html>
<html lang="en">
<head>
<meta charset="UTF-8">
<title>Vexmora-Kin Brochure Cover</title>
<link rel="stylesheet" href="https://fonts.googleapis.com/css2?family=Oswald:wght@400;600;700&family=Roboto+Condensed:wght@700&display=swap">
<style>
  :root {
    --maroon-deep: #2b0c10;
    --maroon: #5a1b22;
    --maroon-light: #8a3a42;
    --red: #c41a22;
    --red-dark: #8e1016;
    --grey-dark: #3a3a3c;
    --grey: #7a7a7c;
    --grey-light: #b9b9bb;
    --white: #ffffff;
    --ink: #1c1c1e;
    --tab: #2a2a2c;
  }
  html, body {
    margin: 0;
    padding: 0;
    width: 900px;
    height: 1200px;
    overflow: hidden;
    background: var(--white);
  }
  .cover {
    position: relative;
    width: 900px;
    height: 1200px;
    overflow: hidden;
    background: linear-gradient(160deg, var(--maroon) 0%, var(--maroon-deep) 70%);
  }
  .cover-art {
    position: absolute;
    inset: 0;
    width: 900px;
    height: 1200px;
  }
  .brand {
    position: absolute;
    top: 220px;
    left: 60px;
    display: flex;
    align-items: center;
    gap: 16px;
  }
  .brand-dot {
    width: 48px;
    height: 48px;
    border-radius: 50%;
    background: var(--white);
  }
  .brand-name {
    font-family: "Oswald", sans-serif;
    font-weight: 400;
    font-size: 50px;
    letter-spacing: 4px;
    color: var(--white);
    line-height: 1;
  }
  .headline {
    position: absolute;
    top: 430px;
    left: 60px;
    margin: 0;
    font-family: "Roboto Condensed", sans-serif;
    font-weight: 700;
    font-size: 112px;
    line-height: 0.95;
    color: var(--white);
    text-transform: uppercase;
    letter-spacing: -1px;
  }
  .tagline {
    position: absolute;
    top: 1100px;
    left: 60px;
    margin: 0;
    font-family: "Oswald", sans-serif;
    font-weight: 700;
    font-size: 30px;
    letter-spacing: 1px;
    color: var(--ink);
    text-transform: uppercase;
  }
  .web-tab {
    position: absolute;
    top: 960px;
    right: 0;
    width: 300px;
    height: 46px;
    background: var(--tab);
    color: var(--white);
    font-family: "Oswald", sans-serif;
    font-weight: 400;
    font-size: 20px;
    letter-spacing: 2px;
    display: flex;
    align-items: center;
    justify-content: center;
  }
</style>
</head>
<body>
  <main class="cover">
    <svg class="cover-art" viewBox="0 0 900 1200" xmlns="http://www.w3.org/2000/svg">
      <defs>
        <linearGradient id="player-photo" x1="0" y1="0" x2="0.6" y2="1">
          <stop offset="0" stop-color="#6e2a31"/>
          <stop offset="0.55" stop-color="#8a4a50"/>
          <stop offset="1" stop-color="#d9b8bb"/>
        </linearGradient>
        <linearGradient id="floor-photo" x1="0" y1="0" x2="1" y2="1">
          <stop offset="0" stop-color="#4a4a4c"/>
          <stop offset="0.6" stop-color="#8c8c8e"/>
          <stop offset="1" stop-color="#c4c4c6"/>
        </linearGradient>
        <linearGradient id="red-band" x1="0" y1="0" x2="1" y2="1">
          <stop offset="0" stop-color="#c41a22"/>
          <stop offset="1" stop-color="#8e1016"/>
        </linearGradient>
      </defs>
      <polygon class="photo-player" role="img" aria-label="Photo of a player wearing a VR headset, backpack PC and hand controllers"
               points="330,0 900,0 900,930 640,960 330,420" fill="url(#player-photo)"/>
      <polygon class="photo-floor" role="img" aria-label="Photo of the arena floor"
               points="0,620 560,1000 0,1080" fill="url(#floor-photo)"/>
      <polygon class="band-red" points="0,430 140,430 700,980 560,1000 0,620" fill="url(#red-band)"/>
      <polygon class="band-shadow" points="140,430 330,420 640,960 700,980" fill="#2b0c10" opacity="0.55"/>
      <polygon class="base-panel" points="0,1080 900,930 900,1200 0,1200" fill="#ffffff"/>
      <polygon class="corner-red" points="0,1130 0,1200 90,1200" fill="#c41a22"/>
    </svg>

    <div class="brand">
      <span class="brand-dot"></span>
      <span class="brand-name">VEXMORA-KIN</span>
    </div>

    <h1 class="headline">Because<br>That’s<br>Where<br>All The<br>Fun Is</h1>

    <div class="web-tab">www.vexmora-kin.com</div>

    <p class="tagline">Fully immersive with walking ability</p>
  </main>
</body>
</html>
```